New Business Card Design Project

We require a business card design for Vexalund, a newly established Indian company.
Our focus is on the development, manufacturing, and export of a diverse array of pharmaceutical products on a global scale. The card should convey a professional appearance, as our primary markets are in Africa, China, and Southeast Asian nations.
We envision a two-sided business card, with the reverse side dedicated to a logo set against a solid color or an elegantly designed pattern. The corners should be rounded. We would appreciate seeing both horizontal and vertical design options. We trust the designer to utilize their expertise in creating this design.

The content for the business card is included in the attached Word file.

Target Market(s)

Our primary markets are in Africa, China, and Southeast Asian, Latin America, Maldives, Sri Lanka

Industry/Entity Type

Pharmaceutical Manufacturing and Export

Contact Information for Business Card

Colors

Designer to choose colors to be used in the design.

Requirements
Must have
• The reverse side of the business card features solely the logo along with the tagline, "Wellness for All."
Should not have
• The logo should not exceed two instances, encompassing both the front and back sides of the card.

```html
<!DOCTYPE html>
<html lang="en">
<head>
<meta charset="utf-8">
<title>Vexalund Business Card</title>
<link rel="stylesheet" href="https://fonts.googleapis.com/css2?family=Montserrat:wght@700;800&family=Nunito+Sans:wght@400;600&display=swap">
<style>
  :root {
    --brand-blue: #22a0d8;
    --brand-red: #e85a45;
    --card-white: #f7f7f7;
    --card-shade: #e9e9ea;
    --ink: #3a3a3c;
    --backdrop: #2b2b2d;
  }
  * { box-sizing: border-box; margin: 0; padding: 0; }
  html, body { width: 1200px; height: 900px; overflow: hidden; }
  body {
    background: var(--backdrop);
    font-family: "Nunito Sans", sans-serif;
    position: relative;
  }
  .card {
    position: absolute;
    left: 250px;
    width: 700px;
    height: 400px;
    border-radius: 30px;
    overflow: hidden;
    background: linear-gradient(160deg, #ffffff 0%, var(--card-white) 55%, var(--card-shade) 100%);
    box-shadow: 0 14px 30px rgba(0,0,0,.45);
  }
  .card--back { top: 35px; }
  .card--front { top: 465px; }
  .card__bands { position: absolute; inset: 0; width: 100%; height: 100%; }
  .band--blue { fill: var(--brand-blue); }
  .band--red { fill: var(--brand-red); }
  .brand-name {
    position: absolute;
    font-family: "Montserrat", sans-serif;
    font-weight: 800;
    color: var(--brand-blue);
    letter-spacing: -1px;
    line-height: 1;
    display: flex;
    align-items: center;
    gap: 12px;
    white-space: nowrap;
  }
  .brand-name__dot {
    width: 16px; height: 16px; border-radius: 50%;
    background: var(--brand-red);
  }
  .card--back .brand-name { left: 70px; top: 150px; font-size: 76px; }
  .card--front .brand-name { right: 50px; top: 115px; font-size: 56px; }
  .web-address {
    position: absolute;
    right: 60px; top: 245px;
    font-family: "Montserrat", sans-serif;
    font-weight: 700;
    font-size: 15px;
    letter-spacing: 7px;
    color: var(--ink);
  }
  .tagline {
    position: absolute;
    font-family: "Montserrat", sans-serif;
    font-weight: 700;
    font-size: 21px;
    letter-spacing: .5px;
    color: #fff;
    text-transform: uppercase;
    white-space: nowrap;
  }
  .card--back .tagline { left: 55px; top: 345px; }
  .card--front .tagline { right: 45px; top: 300px; }
  .contact { position: absolute; left: 50px; top: 50px; color: var(--ink); }
  .contact__name {
    font-family: "Montserrat", sans-serif;
    font-weight: 700;
    font-size: 25px;
    color: var(--brand-blue);
    text-transform: uppercase;
  }
  .contact__role, .contact__company { font-size: 19px; line-height: 1.25; }
  .contact__address { font-size: 19px; line-height: 1.25; margin-top: 18px; padding-left: 30px; }
  .contact__lines { list-style: none; margin-top: 18px; padding-left: 30px; }
  .contact__lines li { display: flex; align-items: center; gap: 10px; font-size: 19px; line-height: 1.35; }
  .contact__icon { width: 18px; height: 18px; fill: none; stroke: var(--brand-blue); stroke-width: 1.8; }
</style>
</head>
<body>

<section class="card card--back" aria-label="Card reverse">
  <svg class="card__bands" viewBox="0 0 700 400" aria-hidden="true">
    <rect class="band--blue" x="0" y="345" width="700" height="55"/>
    <path class="band--red" d="M0,400 L0,330 C0,305 25,292 65,292 L290,292 L400,400 Z"/>
  </svg>
  <div class="brand-name">Vexalund<span class="brand-name__dot"></span></div>
  <div class="web-address">www.vexalund.com</div>
  <div class="tagline">Wellness for All</div>
</section>

<section class="card card--front" aria-label="Card front">
  <svg class="card__bands" viewBox="0 0 700 400" aria-hidden="true">
    <rect class="band--blue" x="0" y="345" width="700" height="55"/>
    <path class="band--red" d="M700,400 L700,250 L445,250 C425,250 412,262 410,282 L398,400 Z"/>
  </svg>
  <div class="brand-name">Vexalund<span class="brand-name__dot"></span></div>
  <div class="contact">
    <h1 class="contact__name">Rohan K. Malvade</h1>
    <p class="contact__role">CEO</p>
    <p class="contact__company">Vexalund</p>
    <p class="contact__address">12, Sunrise Colony<br>Nashik, 422001, India</p>
    <ul class="contact__lines">
      <li><svg class="contact__icon" viewBox="0 0 18 18" aria-hidden="true"><rect x="4.5" y="1.5" width="9" height="15" rx="1.5"/><line x1="8" y1="14" x2="10" y2="14"/></svg>+919812345670</li>
      <li><svg class="contact__icon" viewBox="0 0 18 18" aria-hidden="true"><circle cx="9" cy="9" r="7.5"/><ellipse cx="9" cy="9" rx="3.2" ry="7.5"/><line x1="1.5" y1="9" x2="16.5" y2="9"/></svg>www.vexalund.com</li>
      <li><svg class="contact__icon" viewBox="0 0 18 18" aria-hidden="true"><rect x="1.5" y="4" width="15" height="10" rx="1"/><polyline points="1.5,4 9,10 16.5,4"/></svg>rmalvade@vexalund.com</li>
    </ul>
  </div>
  <div class="tagline">Wellness for All</div>
</section>

</body>
</html>
```